Building company buisness cards

We are looking for a sharp modern new look for our business cards.
We are a New Zealand based company that specialises in house and land packages.
We have attached a photo of the current logo and would like to see if it can be improved somehow if needed.
We are open to any colours but we have chosen green at this stage.
Feel free to change the font and make the logo smarter looking.
Play with the colours and see what looks best.

We want a card that looks so good know one will want to throw it away!

Target Market(s)

Home buyers

Industry/Entity Type

Building

Contact Information for Business Card

Derek Tolvane
0217394062
dtolvane@quillmarkhomesteads.co.nz
quillmarkhomesteads.co.nz

Font styles to use
Serif
Sans Serif

Colors

Designer to choose colors to be used in the design.

Requirements
Must have
• Logo and company name on one side, details on the other side
Nice to have
• Color codes for the original green are HEX #4a8028, RGB(74,128,40), CMYK(42,0,69,50)
• Round corners, Raised and/or spot UV

```html
<!DOCTYPE html>
<html lang="en">
<head>
<meta charset="utf-8">
<title>Quillmark Homesteads – Business Cards</title>
<link href="https://fonts.googleapis.com/css2?family=Montserrat:wght@600&family=Roboto:wght@400&display=swap" rel="stylesheet">
<style>
  :root {
    --brand-green: #4a8028;
    --card-white: #ffffff;
    --backdrop: #a3a3a3;
    --text-grey: #555555;
    --muted-grey: #777777;
  }
  * { margin: 0; padding: 0; box-sizing: border-box; }
  html, body { width: 1200px; height: 930px; overflow: hidden; }
  body {
    background: var(--backdrop);
    position: relative;
    font-family: "Roboto", Arial, sans-serif;
  }
  .card {
    position: absolute;
    width: 540px;
    height: 309px;
    border-radius: 22px;
    box-shadow: 0 6px 14px rgba(0,0,0,0.25);
    overflow: hidden;
  }
  .brand {
    display: flex;
    align-items: center;
  }
  .brand-mark { flex: none; }
  .brand-name {
    font-family: "Montserrat", Arial, sans-serif;
    font-weight: 600;
    white-space: nowrap;
    line-height: 1;
  }
  /* Front */
  .card-front {
    left: 80px; top: 90px;
    background: var(--brand-green);
    color: var(--card-white);
  }
  .front-brand {
    position: absolute;
    left: 0; right: 0; top: 134px;
    justify-content: center;
    gap: 14px;
  }
  .front-brand .brand-mark { width: 24px; height: 24px; background: var(--card-white); }
  .front-brand .brand-name { font-size: 30px; }
  .front-web {
    position: absolute;
    left: 0; right: 0; bottom: 34px;
    text-align: center;
    font-size: 12px;
    letter-spacing: 0.3px;
  }
  /* Back */
  .card-back {
    left: 600px; top: 520px;
    background: var(--card-white);
    color: var(--brand-green);
  }
  .back-brand {
    position: absolute;
    left: 34px; top: 58px;
    gap: 10px;
  }
  .back-brand .brand-mark { width: 16px; height: 16px; background: var(--brand-green); }
  .back-brand .brand-name { font-size: 17px; }
  .holder {
    position: absolute;
    right: 34px; top: 34px;
    width: 200px;
    text-align: right;
    border-bottom: 1px solid var(--brand-green);
    padding-bottom: 8px;
  }
  .holder-name {
    font-family: "Montserrat", Arial, sans-serif;
    font-weight: 600;
    font-size: 22px;
    line-height: 1;
    white-space: nowrap;
  }
  .holder-role { font-size: 10px; color: var(--muted-grey); margin-top: 2px; }
  .contacts {
    position: absolute;
    left: 34px; bottom: 26px;
    width: 260px;
    border-top: 1px solid var(--brand-green);
    padding-top: 12px;
    list-style: none;
    font-size: 12.5px;
    color: var(--text-grey);
  }
  .contacts li { display: flex; align-items: center; gap: 8px; line-height: 20px; white-space: nowrap; }
  .contacts svg { width: 11px; height: 11px; flex: none; }
  .web-domain { color: var(--brand-green); }
</style>
</head>
<body>
  <section class="card card-front" aria-label="Card front">
    <div class="brand front-brand">
      <span class="brand-mark"></span>
      <p class="brand-name">Quillmark Homesteads</p>
    </div>
    <p class="front-web">www.quillmarkhomesteads.co.nz</p>
  </section>

  <section class="card card-back" aria-label="Card back">
    <div class="brand back-brand">
      <span class="brand-mark"></span>
      <p class="brand-name">Quillmark Homesteads</p>
    </div>
    <div class="holder">
      <p class="holder-name">Derek Tolvane</p>
      <p class="holder-role">Founder</p>
    </div>
    <ul class="contacts">
      <li>
        <svg viewBox="0 0 24 24" aria-hidden="true"><path fill="#4a8028" d="M6.6 10.8a15 15 0 0 0 6.6 6.6l2.2-2.2a1 1 0 0 1 1-.25 11.4 11.4 0 0 0 3.6.57 1 1 0 0 1 1 1V20a1 1 0 0 1-1 1A17 17 0 0 1 3 4a1 1 0 0 1 1-1h3.5a1 1 0 0 1 1 1c0 1.25.2 2.45.57 3.57a1 1 0 0 1-.25 1z"/></svg>
        0217394062
      </li>
      <li>
        <svg viewBox="0 0 24 24" aria-hidden="true"><rect x="2" y="5" width="20" height="14" rx="1.5" fill="none" stroke="#4a8028" stroke-width="2.4"/><path d="M2 6l10 7 10-7" fill="none" stroke="#4a8028" stroke-width="2.4"/></svg>
        dtolvane@quillmarkhomesteads.co.nz
      </li>
      <li>
        <svg viewBox="0 0 24 24" aria-hidden="true"><circle cx="12" cy="12" r="10" fill="#4a8028"/><path d="M2 12h20M12 2c3 3 3 17 0 20M12 2c-3 3-3 17 0 20" fill="none" stroke="#fff" stroke-width="1.4"/></svg>
        <span>www.<span class="web-domain">quillmarkhomesteads</span>.co.nz</span>
      </li>
    </ul>
  </section>
</body>
</html>
```